Slogan
Zielgruppe
Wir sind ein Familienhotel in Österreich. Unsere Zielgruppe sind Familien und auch Paare. Unsere Hauptthemen sind im Sommer wandern und im Winter skifahren.
Aufgabenstellung
Es soll aus dem Claim hervorgehen, dass wir besonders Familien ansprechen. Wir sind jedoch kein reines Kinderhotel. Es sind bei uns auch Paare willkommen.

```html
<!DOCTYPE html>
<html lang="de">
<head>
<meta charset="utf-8">
<title>Slogan – Familienhotel</title>
<link rel="stylesheet" href="https://fonts.googleapis.com/css2?family=Arimo&display=swap">
<style>
  :root {
    --paper: #ffffff;
    --claim-blue: #1a93c6;
  }
  html, body {
    margin: 0;
    padding: 0;
    width: 1200px;
    height: 1200px;
    overflow: hidden;
    background: var(--paper);
  }
  .canvas {
    width: 1200px;
    height: 1200px;
    position: relative;
    background: var(--paper);
  }
  .claim {
    position: absolute;
    left: 0;
    right: 0;
    top: 568px;
    margin: 0;
    text-align: center;
    font-family: "Arimo", Arial, sans-serif;
    font-weight: 400;
    font-size: 31px;
    line-height: 40px;
    color: var(--claim-blue);
  }
</style>
</head>
<body>
  <main class="canvas">
    <p class="claim">Hier fühlen sich Familien und Paare gleichermaßen wohl</p>
  </main>
</body>
</html>
```